Stationery Design Project

We need a stationery design for our Norwegian trucking company. We have existed for about 15 years and our 12 drivers uses relatively new vehicles to transport goods around in northern Norway. Long distance routes with fresh fish og food transport is our main operations.

We have already made alogo that's printed on our trucks. The logo and a picture of our trucks is attached. I think the logo i crappy, but since its already in use, changing it is not an option in this round. Still using a better colour scheme in the overall stationery and more interesting fonts is possible (altso in the logo).

Company details:
Name: Kjelvraket AS
Organisation nr 873 615 309
Post adress: 8642 Raudvik

I like minimalism and simplicity. I am avalibly for questions in normal GMT working hours either here or on mail: ivar@fjordlast.no

Reason: Hi. Im extending the deadline because I needed some time to find a vector file of our logo. Sorry for the inconvenience

Hi, and thanks for all your interest in the project. Some updates:

-          I have decided to commit to using one of the designs. Some designer will get the payment.

-          I have extended the deadline with 24 hours since I needed some time to find our firms vector logo (a slow Swedish man was holding me up)

-          We will not choose a design before the deadline. No need to rush.

-          We have received a lot of great design and think there is a need to specified the product we want to make:

o   Business Card for all our employers. I just need the design and will duplicate with the correct numbers and name myself. The information on should be: Logo, employer’s name, Phone number, email, website, Postal number and address. Use this as a template: logo, Leif Brattvoll, 47382066, Leif@fjordlast.no,, fjordlast.no, 8642 Raudvik. The order and placement of the information is your creative decision.

o   Stickers to put on the goods we travel. On the sticker the should be the following information: Logo, phone number, Tekst and link: Fraktæ av Kjelvraket. Ke du syns? Fjordlast.no/tilbakemelding (this means: Handled by Kjelvraket. What do you think Fjordlast.no/feedback -à the link will be a feedback form). The placement the information and size is your creative decision with some stings: we have been thinking of using Drukko for printing and see that a size about 6x6 cm, 8x5 or something like that. (with 3000 copies our budget is 200 punds). Any suggestions of other suppliers are welcome. Drukko price calculator http://www.drukkolabelhouse.co.uk/digital-litho-printing/printing-labels-tags/stickers/

o   Letterhead with logo, address, phone number and organizational number.

o   Envelopes with logo,address, phone number and organizational number.

Have a nice day.

 

 

• Using the blue colour in the logo and using a similar graphic approch.

```html
<!DOCTYPE html>
<html lang="no">
<head>
<meta charset="utf-8">
<title>Kjelvraket – business cards</title>
<link href="https://fonts.googleapis.com/css2?family=Open+Sans:wght@400;700&family=Tinos:wght@400;700&display=swap" rel="stylesheet">
<style>
  :root {
    --bg: #d6d8db;
    --white: #ffffff;
    --brand-blue: #0b4ea2;
    --bright-blue: #0a70bb;
    --wave-light: #1a73c4;
    --ink-grey: #3a3a3a;
    --dark-text: #222222;
  }
  * { margin: 0; padding: 0; box-sizing: border-box; }
  html, body { width: 1200px; height: 751px; overflow: hidden; }
  body { background: var(--bg); position: relative; font-family: "Open Sans", Arial, sans-serif; }

  .card {
    position: absolute;
    width: 525px;
    height: 298px;
    overflow: hidden;
    box-shadow: 0 1px 4px rgba(0,0,0,0.35);
  }
  .card--front { left: 44px; top: 61px; background: var(--white); }
  .card--bright { left: 616px; top: 65px; background: var(--bright-blue); }
  .card--deep { left: 44px; top: 390px; background: var(--brand-blue); }
  .card--light { left: 616px; top: 390px; background: var(--white); }

  .brand {
    position: absolute;
    display: flex;
    align-items: center;
    gap: 14px;
    font-family: "Open Sans", Arial, sans-serif;
    font-weight: 700;
    font-size: 44px;
    letter-spacing: 0.5px;
    line-height: 1;
  }
  .brand__dot { width: 26px; height: 26px; border-radius: 50%; background: currentColor; flex: none; }
  .card--front .brand { left: 48px; top: 58px; color: var(--brand-blue); }
  .card--bright .brand, .card--deep .brand { color: var(--white); }
  .card--light .brand { color: var(--brand-blue); }
  .card--bright .brand, .card--deep .brand, .card--light .brand {
    left: 0; right: 0; top: 120px; justify-content: center;
  }

  .site {
    position: absolute;
    left: 0; right: 0; top: 246px;
    text-align: center;
    font-size: 17px;
    letter-spacing: 4px;
  }
  .card--bright .site, .card--deep .site { color: var(--white); }
  .card--light .site { color: var(--dark-text); }

  .wave { position: absolute; left: 0; top: 0; }

  .person {
    position: absolute;
    left: 49px; top: 170px;
    font-family: "Tinos", "Times New Roman", serif;
  }
  .person__name { font-size: 22px; font-weight: 700; color: var(--brand-blue); }
  .person__address { margin-top: 4px; font-size: 16px; color: var(--ink-grey); display: flex; align-items: center; gap: 5px; }

  .contact {
    position: absolute;
    right: 24px; top: 198px;
    list-style: none;
    text-align: right;
    color: var(--white);
    font-size: 14px;
    line-height: 21px;
  }
  .contact li { display: flex; justify-content: flex-end; align-items: center; gap: 5px; }
  .contact svg { flex: none; }
</style>
</head>
<body>

  <section class="card card--front">
    <svg class="wave" width="525" height="298" viewBox="0 0 525 298" aria-hidden="true">
      <path d="M0,222 C150,300 320,250 525,126 L525,298 L0,298 Z" fill="var(--wave-light)"/>
      <path d="M0,238 C150,305 330,262 525,140 L525,298 L0,298 Z" fill="var(--white)"/>
      <path d="M0,248 C160,300 330,268 525,148 L525,298 L0,298 Z" fill="var(--brand-blue)"/>
      <path d="M0,268 C120,300 230,280 320,240" fill="none" stroke="var(--wave-light)" stroke-width="6"/>
    </svg>

    <div class="brand"><span class="brand__dot"></span>Kjelvraket</div>

    <div class="person">
      <p class="person__name">Leif Brattvoll</p>
      <p class="person__address">
        <svg width="12" height="10" viewBox="0 0 12 10" aria-hidden="true"><path d="M1,5 L6,1 L11,5 L11,9 L1,9 Z" fill="none" stroke="var(--ink-grey)" stroke-width="1.3"/></svg>
        8642 Raudvik
      </p>
    </div>

    <ul class="contact">
      <li><svg width="11" height="11" viewBox="0 0 12 12" aria-hidden="true"><path d="M2,1 L4,1 L5,4 L3.5,5 C4.5,7 5,7.5 7,8.5 L8,7 L11,8 L11,10 C11,11 10,11 9,11 C4,10 2,8 1,3 C1,2 1,1 2,1 Z" fill="var(--white)"/></svg>47382066</li>
      <li>Org nr 873 615 309</li>
      <li><svg width="11" height="9" viewBox="0 0 12 9" aria-hidden="true"><rect x="0.5" y="0.5" width="11" height="8" fill="var(--white)"/><path d="M0.5,0.5 L6,5 L11.5,0.5" fill="none" stroke="var(--brand-blue)" stroke-width="1"/></svg>Leif@fjordlast.no</li>
      <li><svg width="11" height="11" viewBox="0 0 12 12" aria-hidden="true"><circle cx="6" cy="6" r="5" fill="none" stroke="var(--white)" stroke-width="1.2"/><path d="M1,6 H11 M6,1 C3,4 3,8 6,11 M6,1 C9,4 9,8 6,11" fill="none" stroke="var(--white)" stroke-width="1"/></svg>www.fjordlast.no</li>
    </ul>
  </section>

  <section class="card card--bright">
    <div class="brand"><span class="brand__dot"></span>Kjelvraket</div>
    <p class="site">www.fjordlast.no</p>
  </section>

  <section class="card card--deep">
    <div class="brand"><span class="brand__dot"></span>Kjelvraket</div>
    <p class="site">www.fjordlast.no</p>
  </section>

  <section class="card card--light">
    <div class="brand"><span class="brand__dot"></span>Kjelvraket</div>
    <p class="site">www.fjordlast.no</p>
  </section>

</body>
</html>
```